Flat bootstrap design for existing site

I'm looking for a modern flat design based around an existing logo. This has to be a custom design (no external templates), and implemented into a bootstrap framework.

The logo is attached as 2 versions - choose whichever you want, that flows better with whatever design you choose.

Added screenshots of the existing site (currently using the default bootstrap layouts). Please make your designs around those pages in the screenshots (i.e. the homepage only has the postal code input and the header). The active page has 3 screenshots, because I wanted to illustrate the other states that would be visible (in the table rows).

This is a moving/junk removal website, just for some context.

Here's some example websites (flat designs) that I like, just to give you an idea of what I'm after.

https://www.plimvora.com/
https://dacklow.com/
https://trevanu.com/
https://quobrintal.com/en/

Coding

Coded - Design and coding required

Number of Pages Required

5+ page

Colors

Designer to choose colors to be used in the design.

Requirements
Must have
• It must be a modern/simple flat design, that is built around the existing logo (attached).
• It has to be implemented using bootstrap.

```html
<!DOCTYPE html>
<html lang="en">
<head>
<meta charset="utf-8">
<title>Haulvo – Booking Details</title>
<link href="https://fonts.googleapis.com/css2?family=Open+Sans:wght@400;600;700&display=swap" rel="stylesheet">
<style>
  :root {
    --sky: #3fbcf0;
    --sky-dark: #2ba4d9;
    --navy: #1b2140;
    --page: #f2f2f2;
    --white: #ffffff;
    --ink: #333333;
    --muted-ink: #3f5a6f;
    --info-bg: #e6f2f9;
    --table-head: #139bea;
    --row: #ececec;
    --field-border: #b9b9b9;
    --ok: #5fa24a;
    --sent: #5cb0d6;
    --pending: #666666;
    --pay: #2f62a3;
  }
  * { box-sizing: border-box; margin: 0; padding: 0; }
  html, body { width: 1200px; height: 649px; overflow: hidden; }
  body {
    background: var(--page);
    font-family: "Open Sans", Arial, sans-serif;
    color: var(--ink);
    position: relative;
  }
  .site-header {
    height: 70px;
    background: var(--sky);
    display: flex;
    align-items: center;
    padding: 0 21px;
  }
  .brand {
    display: flex; align-items: center; gap: 8px;
    color: var(--white); font-weight: 700; font-size: 24px; letter-spacing: 1px;
  }
  .brand-dot { width: 12px; height: 12px; border-radius: 50%; background: var(--white); }
  .main-nav { margin-left: auto; display: flex; align-items: center; height: 100%; }
  .main-nav a {
    color: var(--white); text-decoration: none; font-size: 13px;
    padding: 9px 19px; line-height: 17px;
  }
  .main-nav a.nav-cta { background: var(--sky-dark); border-radius: 2px; margin: 0 12px 0 14px; }
  .main-nav a.nav-user { padding-right: 0; }

  .panel { position: absolute; left: 22px; width: 1156px; background: var(--white); }
  .panel-title {
    height: 42px; background: var(--navy); color: var(--white);
    font-size: 16px; font-weight: 600; line-height: 42px; padding-left: 20px;
  }
  .booking { top: 99px; height: 147px; }
  .booking-form { position: relative; height: 105px; }
  .field { position: absolute; top: 23px; }
  .field label { display: block; font-size: 11px; margin-bottom: 7px; }
  .field-box {
    height: 36px; border: 1px solid var(--field-border); background: var(--white);
    font-size: 10px; padding: 0 13px; display: flex; align-items: center; justify-content: space-between;
  }
  .field-package { left: 20px; width: 226px; }
  .field-time { left: 260px; width: 226px; }
  .field-desc { left: 500px; width: 544px; }
  .btn-update {
    position: absolute; left: 1058px; top: 56px; width: 78px; height: 36px;
    background: var(--sky); color: var(--white); border: 0;
    font-family: inherit; font-size: 14px; font-weight: 600; letter-spacing: .5px;
  }

  .drivers { top: 268px; height: 330px; }
  .notice {
    position: absolute; left: 20px; top: 63px; width: 1116px; height: 49px;
    background: var(--info-bg); color: var(--muted-ink);
    font-size: 11px; line-height: 49px; padding-left: 20px;
  }
  .driver-table {
    position: absolute; left: 20px; top: 127px; width: 1116px;
    border-collapse: collapse; font-size: 10px;
  }
  .driver-table th {
    background: var(--table-head); color: var(--white); font-weight: 400;
    font-size: 11px; height: 35px; text-align: left;
  }
  .driver-table td { background: var(--row); height: 37px; border-top: 2px solid var(--white); }
  .driver-table tr:first-child td { border-top: 0; }
  .col-name { width: 169px; padding-left: 20px; }
  .col-dist { width: 190px; }
  .col-time { width: 248px; }
  .col-status { width: 241px; }
  .tag {
    display: inline-block; width: 96px; height: 20px; line-height: 20px;
    text-align: center; color: var(--white); font-size: 10px;
  }
  .tag-ok { background: var(--ok); }
  .tag-sent { background: var(--sent); }
  .tag-pending { background: var(--pending); }
  .btn-pay { background: var(--pay); }

  .site-footer {
    position: absolute; top: 618px; width: 100%; text-align: center; font-size: 9px; color: var(--ink);
  }
</style>
</head>
<body>
  <header class="site-header">
    <div class="brand"><span class="brand-dot"></span>HAULVO</div>
    <nav class="main-nav">
      <a href="#">Book</a>
      <a href="#">How It Works</a>
      <a href="#" class="nav-cta">Become a Driver</a>
      <a href="#" class="nav-user">sam@mailbrook.com</a>
    </nav>
  </header>

  <section class="panel booking">
    <h2 class="panel-title">Booking Details</h2>
    <div class="booking-form">
      <div class="field field-package">
        <label>Package selected :</label>
        <div class="field-box">Package 1
          <svg width="10" height="6" viewBox="0 0 10 6"><path d="M0 0h10L5 6z" fill="#555"/></svg>
        </div>
      </div>
      <div class="field field-time">
        <label>Pick-up time selected :</label>
        <div class="field-box">July 18 at 4:13 am
          <svg width="14" height="14" viewBox="0 0 14 14" fill="none" stroke="#666" stroke-width="1">
            <rect x="1" y="2" width="12" height="11"/><path d="M1 5h12M4 0.5v3M10 0.5v3M4 7.5h1M7 7.5h1M10 7.5h1M4 10h1M7 10h1M10 10h1"/>
          </svg>
        </div>
      </div>
      <div class="field field-desc">
        <label>Description :</label>
        <div class="field-box">1 large stove</div>
      </div>
      <button class="btn-update">UPDATE</button>
    </div>
  </section>

  <section class="panel drivers">
    <h2 class="panel-title">Drivers in your area</h2>
    <p class="notice">Please stay on this page and be patient, while we contact the drivers and find you one ASAP.</p>
    <table class="driver-table">
      <thead>
        <tr><th class="col-name">Name</th><th class="col-dist">Distance (km)</th><th class="col-time">Agreed pick-up time</th><th class="col-status"></th><th></th></tr>
      </thead>
      <tbody>
        <tr><td class="col-name">Owen Marsh</td><td>4.04km away</td><td>July 18 at 4:13 am</td><td><span class="tag tag-ok">Time accepted</span></td><td><span class="tag btn-pay">Make payment</span></td></tr>
        <tr><td class="col-name">Peter Vale</td><td>5.7km away</td><td>-</td><td><span class="tag tag-sent">Request Sent</span></td><td></td></tr>
        <tr><td class="col-name">Rufus Hale</td><td>11.13km away</td><td>-</td><td><span class="tag tag-sent">Request Sent</span></td><td></td></tr>
        <tr><td class="col-name">Colin Barrow</td><td>11.91km away</td><td>-</td><td><span class="tag tag-pending">Pending</span></td><td></td></tr>
      </tbody>
    </table>
  </section>

  <footer class="site-footer">Copyright &copy; 2017 Haulvo. All rights reserved.</footer>
</body>
</html>
```